Stabilization Flyer

We are looking for a single document that outlines the info below - we want to emphasize that we can help child cares in the process and then we can help them make any award money go further through our program -
Don’t leave money on the table – as a child care owner you have access to grant money, but time is running out.

President Harlow signed the National Renewal Fund Act of 2021 (NRF). This plan includes $24 billion in child care stabilization grant funding. These funds will help keep early childhood educators and family child care providers keep their doors open and provide a critical step to paving the way for a strong economic recovery and a more equitable future.

Each State has its own application process – most licensed child care centers are eligible for grants with awards up to $400,000 per program. Awarded dollars is based upon your center’s capacity.

Grants are good for the following categories

Child care providers can use stabilization subgrants to cover these expenses:
• Wages and benefits, including increases in compensation for any staff.
• Rent, utilities, facilities maintenance and minor renovations, and insurance.
• Personal protective equipment, cleaning supplies, and other health and safety measures.
• Equipment and supplies used to respond to COVID-19.
• Material goods (i.e., to facilitate play or safe sleep) or services (i.e., food) used for the operation of the program. Yes, Food is an allowable expense.
• Mental health services for children and employees

If you have not applied for the grant, we can help point you in the right direction. Just email stablization@pantryhubdirect.com or call 877. 315.6093 and we will send you the links on how to file within your State. No purchase is necessary for this guidance, but we would love the opportunity to show you how we can stretch your purchases by up to 30%.

Target Market(s)

child care centers

Industry/Entity Type

child care is the target

Requirements
Must have
• website www.pantryhubdirect.com
Nice to have
• we have a video that could be embedded https://www.pantryhubdirect.com/video-resources/

```html
<!DOCTYPE html>
<html lang="en">
<head>
<meta charset="utf-8">
<title>Stabilization Grant Flyer – Pantry Hub Direct</title>
<link href="https://fonts.googleapis.com/css2?family=Montserrat:wght@400;500;600;700;800&family=Oswald:wght@500;600&display=swap" rel="stylesheet">
<style>
:root{
  --blue:#3a82c9;
  --blue-dark:#24528f;
  --green:#6aa84f;
  --green-bright:#8cdc5a;
  --grey:#6d6e71;
  --grey-light:#ededed;
  --ink:#222;
  --white:#fff;
}
*{margin:0;padding:0;box-sizing:border-box}
html,body{width:783px;height:1200px;overflow:hidden;background:var(--white)}
body{font-family:"Montserrat",Arial,sans-serif;color:var(--ink)}
.flyer{position:relative;width:783px;height:1200px;overflow:hidden;background:var(--white)}

/* header */
.brand{position:absolute;left:42px;top:40px;display:flex;align-items:center;gap:10px}
.brand-mark{width:30px;height:30px;background:var(--blue)}
.brand-name{font-size:25px;font-weight:500;color:var(--blue-dark)}
.accent-line{position:absolute;left:0;top:0}

/* hero */
.hero-panel{position:absolute;left:0;top:122px;width:440px;height:302px;
  background:linear-gradient(180deg,var(--blue) 0%,var(--blue-dark) 100%);
  clip-path:polygon(0 0,388px 0,388px 12px,435px 302px,0 302px)}
.hero-photo{position:absolute;left:390px;top:0;width:393px;height:424px;
  background:linear-gradient(160deg,#d9d2c6 0%,#b9a894 45%,#e8e4de 100%);
  clip-path:polygon(12px 0,393px 0,393px 424px,50px 424px,6px 140px,6px 60px)}
.headline{position:absolute;left:46px;top:146px;width:330px;color:var(--white);text-transform:uppercase;font-weight:700;line-height:1.1}
.headline .l1{font-size:27px;font-weight:800}
.headline .l2{font-size:21px}
.headline .l3{font-size:34px;font-weight:800;color:var(--green-bright)}
.headline .l4{font-size:25px;font-weight:800}
.headline-rule{position:absolute;left:46px;top:316px;width:290px;height:1px;background:rgba(255,255,255,.5)}
.headline-rule::before{content:"";position:absolute;left:35px;top:-2px;width:50px;height:5px;border-radius:3px;background:var(--green-bright)}
.plan-label{position:absolute;left:46px;top:336px;color:var(--white);font-size:13px;font-weight:600;letter-spacing:.5px}
.plan-amount{position:absolute;left:44px;top:352px;display:flex;align-items:center;gap:10px}
.plan-amount .dollars{font-family:"Oswald",Impact,sans-serif;font-size:50px;font-weight:600;color:var(--green-bright);line-height:1}
.plan-pill{display:flex;align-items:stretch;background:var(--white);border-radius:5px;overflow:hidden;height:42px}
.plan-pill .unit{background:var(--green);color:var(--white);font-weight:800;font-size:20px;padding:0 10px;display:flex;align-items:center}
.plan-pill .note{font-size:9px;font-weight:600;line-height:1.2;padding:5px 9px;width:110px;display:flex;align-items:center}

/* intro band */
.intro-band{position:absolute;left:0;top:430px;width:783px;height:92px;background:var(--grey);color:var(--white);
  font-size:12.2px;font-weight:700;line-height:1.35;padding:20px 110px 0 46px}

/* state process */
.state-card{position:absolute;left:48px;top:542px;width:305px;z-index:2}
.state-tab{background:var(--blue);color:var(--white);font-size:13px;font-weight:800;line-height:1.2;padding:8px 18px;
  border-radius:8px 0 0 0;clip-path:polygon(0 0,100% 0,92% 100%,0 100%)}
.state-tab span{display:block;color:var(--green-bright)}
.state-body{display:flex;align-items:center;background:var(--grey-light);padding:12px 16px}
.state-body .left{flex:0 0 132px;font-size:11.5px;font-weight:600;line-height:1.2;border-right:1px dashed #888;padding-right:8px}
.state-body .right{flex:1;padding-left:12px;font-size:11.5px;font-weight:700;line-height:1.1}
.state-body .right span{display:block}
.state-body .big{font-family:"Oswald",Impact,sans-serif;font-size:28px;font-weight:600;color:var(--green);line-height:1.05}
.state-foot{background:var(--green);color:var(--white);font-size:11px;font-weight:600;text-align:center;line-height:1.3;padding:8px 30px;border-radius:0 0 6px 6px}
.classroom-photo{position:absolute;left:0;top:712px;width:410px;height:210px;z-index:1;
  background:linear-gradient(120deg,#c9b8a6 0%,#e4d7c6 50%,#f3efe9 100%)}

/* categories */
.categories{position:absolute;left:422px;top:545px;width:330px}
.categories h2{font-size:15px;font-weight:800;line-height:1.2;text-transform:uppercase;color:var(--ink)}
.categories h2 span{display:block;color:var(--green)}
.categories ul{list-style:none;margin-top:14px}
.categories li{position:relative;padding-left:34px;font-size:12.5px;font-weight:500;line-height:1.22;margin-bottom:18px}
.categories li::before{content:"";position:absolute;left:4px;top:3px;width:10px;height:10px;background:var(--blue)}

/* call to action */
.help{position:absolute;left:0;top:922px;width:410px;height:158px;background:var(--grey-light);padding:22px 0 0 56px}
.help p{font-size:12px;font-weight:800;line-height:1.3;text-transform:uppercase;letter-spacing:-.3px}
.help p span{color:var(--green)}
.email-row{display:flex;margin-top:22px;height:30px;font-size:11px;font-weight:600}
.email-row .label{background:#b9dea0;color:var(--ink);font-weight:800;font-size:12.5px;padding:0 12px;display:flex;align-items:center;border-radius:4px 0 0 4px}
.email-row .addr{background:var(--blue-dark);color:var(--white);padding:0 10px;display:flex;align-items:center;border-radius:0 4px 4px 0}
.savings{position:absolute;left:410px;top:922px;width:373px;height:158px;background:var(--blue);color:var(--white);display:flex;padding:22px 0 0 28px}
.savings .text{width:190px;font-size:10.5px;font-weight:500;line-height:1.25;border-right:1px dashed rgba(255,255,255,.7);padding-right:10px;height:104px}
.savings .offer{padding-left:16px;font-weight:700;font-size:18px;line-height:1}
.savings .offer .big{display:block;font-family:"Oswald",Impact,sans-serif;font-size:62px;font-weight:600}

/* footer */
.footer-mark{position:absolute;left:22px;top:1110px;width:56px;height:56px;background:var(--blue)}
.footer{position:absolute;left:100px;top:1092px;width:683px;height:108px;background:var(--green);border-radius:8px 0 0 0;color:var(--white);display:flex;align-items:center;padding:0 22px}
.footer .col{display:flex;flex-direction:column;gap:10px}
.footer .col.first{width:310px;border-right:1px dashed rgba(255,255,255,.7);padding-right:10px}
.footer .col.second{padding-left:18px}
.footer .item{display:flex;align-items:center;gap:8px}
.footer .phone{font-size:21px;font-weight:500}
.footer .small{font-size:12px;font-weight:500}
.footer .contact{font-size:15px;font-weight:500}
.footer svg{flex:none}
</style>
</head>
<body>
<main class="flyer">

  <svg class="accent-line" width="783" height="130" aria-hidden="true">
    <line x1="405" y1="0" x2="345" y2="122" stroke="#6aa84f" stroke-width="2.5"/>
  </svg>

  <header class="brand">
    <div class="brand-mark" aria-hidden="true"></div>
    <div class="brand-name">Pantry Hub Direct</div>
  </header>

  <div class="hero-photo" role="img" aria-label="Photo of a doctor giving a high five to a smiling child sitting with his mother"></div>
  <section class="hero-panel" aria-hidden="true"></section>

  <h1 class="headline">
    <div class="l1">President Harlow</div>
    <div class="l2">Signed the National</div>
    <div class="l3">Renewal Fund</div>
    <div class="l4">Act of 2021 (NRF)</div>
  </h1>
  <div class="headline-rule" aria-hidden="true"></div>
  <div class="plan-label">THIS PLAN INCLUDES</div>
  <div class="plan-amount">
    <span class="dollars">$24</span>
    <div class="plan-pill"><span class="unit">BILLION</span><span class="note">In child care stabilization grant funding.</span></div>
  </div>

  <section class="intro-band">
    These funds will help keep early childhood educators and family child care providers keep their doors open and provide a critical step to paving the way for a strong economic recovery and a more equitable future.
  </section>

  <section class="state-card">
    <div class="state-tab">EACH STATE HAS ITS<span>OWN APPLICATION PROCESS</span></div>
    <div class="state-body">
      <div class="left">Most licensed child care centers are eligible for grants with awards</div>
      <div class="right"><span>UP TO</span><span class="big">$400,000</span><span>PER PROGRAM</span></div>
    </div>
    <div class="state-foot">Awarded dollars is based upon your center's capacity.</div>
  </section>
  <div class="classroom-photo" role="img" aria-label="Photo of a teacher and young children playing with a bead maze toy in a classroom"></div>

  <section class="categories">
    <h2>Grants are good for the<span>following categories</span></h2>
    <ul>
      <li>Wages and benefits, including increases in compensation for any staff.</li>
      <li>Rent, utilities, facilities maintenance and minor renovations, and insurance.</li>
      <li>Personal protective equipment, cleaning supplies, and other health and safety measures.</li>
      <li>Equipment and supplies used to respond to COVID-19.</li>
      <li>Material goods (i.e., to facilitate play or safe sleep) or services (i.e., food) used for the operation of the program. Yes, Food is an allowable expense.</li>
      <li>Mental health services for children and employees</li>
    </ul>
  </section>

  <section class="help">
    <p><span>If you have not applied for the grant, we can</span><br>help point you in the right direction.</p>
    <div class="email-row"><span class="label">JUST EMAIL</span><span class="addr">stablization@pantryhubdirect.com</span></div>
  </section>

  <section class="savings">
    <div class="text">We will send you the links on how to file within your State. No purchase is necessary for this guidance, but we would love the opportunity to show you how we can stretch your purchases by</div>
    <div class="offer">up to<span class="big">$30</span></div>
  </section>

  <div class="footer-mark" aria-hidden="true"></div>
  <footer class="footer">
    <div class="col first">
      <div class="item phone">
        <svg width="16" height="16" viewBox="0 0 24 24" aria-hidden="true"><path fill="#fff" d="M6.6 10.8a15.1 15.1 0 0 0 6.6 6.6l2.2-2.2c.3-.3.7-.4 1-.2 1.1.4 2.3.6 3.6.6.6 0 1 .4 1 1V20c0 .6-.4 1-1 1A17 17 0 0 1 3 4c0-.6.4-1 1-1h3.5c.6 0 1 .4 1 1 0 1.2.2 2.4.6 3.6.1.3 0 .7-.2 1z"/></svg>
        877-315-6093
      </div>
      <div class="item small">
        <svg width="12" height="16" viewBox="0 0 12 16" aria-hidden="true"><path fill="#fff" d="M6 0a6 6 0 0 0-6 6c0 4.5 6 10 6 10s6-5.5 6-10a6 6 0 0 0-6-6zm0 8.2A2.2 2.2 0 1 1 6 3.8a2.2 2.2 0 0 1 0 4.4z"/></svg>
        2280 Harbor Mill Road Easton, MA 02375
      </div>
    </div>
    <div class="col second">
      <div class="item contact">
        <svg width="16" height="12" viewBox="0 0 16 12" aria-hidden="true"><rect x=".75" y=".75" width="14.5" height="10.5" fill="none" stroke="#fff" stroke-width="1.5"/><path d="M1 1l7 6 7-6" fill="none" stroke="#fff" stroke-width="1.5"/></svg>
        info@pantryhubdirect.com
      </div>
      <div class="item contact">
        <svg width="16" height="16" viewBox="0 0 16 16" aria-hidden="true"><circle cx="8" cy="8" r="7" fill="none" stroke="#fff" stroke-width="1.4"/><ellipse cx="8" cy="8" rx="3" ry="7" fill="none" stroke="#fff" stroke-width="1.2"/><path d="M1 8h14M2.5 4.5h11M2.5 11.5h11" stroke="#fff" stroke-width="1.1"/></svg>
        www.pantryhubdirect.com
      </div>
    </div>
  </footer>

</main>
</body>
</html>
```